Profesional personal website needs design and business card

I need a business card with my professional name as a logo "Dorian Vitality" for my business. I am a Wellness Coach, consultant and trainer. So it should be professional, wellness oriented and modern.

Target Market(s)

Private clients, governments, corporations. Luxury and high market.

Industry/Entity Type

Health And Wellness

Contact Information for Business Card

Dorian Vitality should be the logo

Colors

Designer to choose colors to be used in the design.

Requirements
Must have
• Dorian Vitality
• Name: Tomás Lirandel
• Wellness Coach, Consultant & Trainer.
• Website: www.dorianvitality-example.com
• Phone:
• Spain (+34) 612 480 317
• (USA) +1 (555) 610 4829
Nice to have
• The most important is the design of "Dorian Vitality", as this is going to be my personal brand logo. It should be professional, wellness, high end and actual.
Should not have
• no golds, no baroque style..

```html
<!DOCTYPE html>
<html lang="en">
<head>
<meta charset="UTF-8">
<title>Dorian Vitality – Business Card</title>
<link href="https://fonts.googleapis.com/css2?family=Lato:wght@400;700;900&display=swap" rel="stylesheet">
<style>
  :root {
    --brand-blue: #1276c0;
    --ink-grey: #4a4a4a;
    --card-white: #ffffff;
    --backdrop: #2a2a2a;
  }
  * { margin: 0; padding: 0; box-sizing: border-box; }
  html, body {
    width: 1200px; height: 878px; overflow: hidden;
    background: var(--backdrop);
    font-family: "Lato", Arial, sans-serif;
  }
  .canvas {
    position: relative; width: 1200px; height: 878px;
  }
  .card {
    position: absolute; left: 320px; width: 560px; height: 320px;
    box-shadow: 0 10px 30px rgba(0,0,0,0.5);
  }
  .card-front { top: 89px; background: var(--brand-blue); color: var(--card-white); }
  .card-back { top: 469px; background: var(--card-white); }

  .front-brand {
    position: absolute; left: 0; right: 0; top: 120px;
    display: flex; flex-direction: column; align-items: center;
  }
  .brand-name {
    display: flex; align-items: center; gap: 14px;
    font-weight: 900; font-size: 38px; letter-spacing: 1px; text-transform: uppercase;
  }
  .brand-mark { width: 18px; height: 18px; background: var(--card-white); }
  .front-url {
    margin-top: 16px; font-size: 14px; letter-spacing: 5px;
  }

  .holder { position: absolute; left: 36px; top: 32px; }
  .holder-name {
    color: var(--brand-blue); font-weight: 900; font-size: 27px; text-transform: uppercase;
  }
  .holder-title { color: var(--ink-grey); font-size: 15px; margin-top: 2px; }

  .contact-list {
    position: absolute; left: 36px; bottom: 28px; list-style: none;
    color: var(--ink-grey); font-size: 16px;
  }
  .contact-list li { display: flex; align-items: center; gap: 12px; height: 26px; }
  .contact-list svg { width: 16px; height: 16px; fill: var(--brand-blue); flex: none; }

  .back-brand {
    position: absolute; right: 34px; bottom: 40px; text-align: right;
    color: var(--brand-blue); font-weight: 900; font-size: 34px; line-height: 1.05;
    text-transform: uppercase;
  }
</style>
</head>
<body>
<main class="canvas">
  <section class="card card-front">
    <div class="front-brand">
      <div class="brand-name"><span class="brand-mark"></span>Dorian Vitality</div>
      <div class="front-url">www.dorianvitality-example.com</div>
    </div>
  </section>

  <section class="card card-back">
    <div class="holder">
      <h1 class="holder-name">Tomás Lirandel</h1>
      <p class="holder-title">Wellness Coach, Consultant &amp; Trainer</p>
    </div>

    <ul class="contact-list">
      <li>
        <svg viewBox="0 0 24 24"><path d="M6.6 10.8a15 15 0 0 0 6.6 6.6l2.2-2.2a1 1 0 0 1 1-.25 11.4 11.4 0 0 0 3.6.57 1 1 0 0 1 1 1V20a1 1 0 0 1-1 1A17 17 0 0 1 3 4a1 1 0 0 1 1-1h3.5a1 1 0 0 1 1 1 11.4 11.4 0 0 0 .57 3.6 1 1 0 0 1-.25 1z"/></svg>
        (+34) 612 480 317 (Spain)
      </li>
      <li>
        <svg viewBox="0 0 24 24"><path d="M6.6 10.8a15 15 0 0 0 6.6 6.6l2.2-2.2a1 1 0 0 1 1-.25 11.4 11.4 0 0 0 3.6.57 1 1 0 0 1 1 1V20a1 1 0 0 1-1 1A17 17 0 0 1 3 4a1 1 0 0 1 1-1h3.5a1 1 0 0 1 1 1 11.4 11.4 0 0 0 .57 3.6 1 1 0 0 1-.25 1z"/></svg>
        +1 (555) 610 4829 (USA)
      </li>
      <li>
        <svg viewBox="0 0 24 24"><path d="M2 5h20v14H2z M3.5 6.5 12 13l8.5-6.5" fill="none" stroke="#1276c0" stroke-width="2"/></svg>
        info@dorianvitality-example.com
      </li>
      <li>
        <svg viewBox="0 0 24 24"><g fill="none" stroke="#1276c0" stroke-width="2"><circle cx="12" cy="12" r="9"/><path d="M3 12h18M12 3c3 3 3 15 0 18M12 3c-3 3-3 15 0 18"/></g></svg>
        www.dorianvitality-example.com
      </li>
    </ul>

    <div class="back-brand">Dorian<br>Vitality</div>
  </section>
</main>
</body>
</html>
```